Brand Identity Stationary Package

Hello I'm looking for a full branding package for my Property Management Company. I have a logo but looking to have the following
Business Card
Email signature
Facebook cover photo
Letterhead (word.doc)
#10 Envelope
Pocket Folder - link to 9x12 pocket folder design specs https://www.printorbit-example.ca/marketing-materials/presentation-folders
would like everything to match and be brand identifiable. The company looks after residential properties/apartments and some commercial properties. Attached is a zip of the files.
For Business Card
Name: Gareth Lindqvist
Position: Operations Manager
Number: 1 (555) 384-2917
Email: Gareth@harborkey-example.ca
Website: Harborkey-example.ca
Property Management

```html
<!DOCTYPE html>
<html lang="en">
<head>
<meta charset="utf-8">
<title>Harborkey Business Card</title>
<link rel="stylesheet" href="https://fonts.googleapis.com/css2?family=Montserrat:wght@600;700&family=Roboto:wght@400;700&display=swap">
<style>
  :root {
    --bg: #d3d6d7;
    --card-white: #f4f4f2;
    --card-black: #141414;
    --ink: #1c1c1c;
    --ink-soft: #3a3a3a;
    --green: #5a9a22;
    --edge-green: #6fae2c;
    --white: #f2f2f2;
    --grey-text: #8b8b8b;
  }
  * { margin: 0; padding: 0; box-sizing: border-box; }
  html, body { width: 1200px; height: 1050px; overflow: hidden; }
  body {
    background: var(--bg);
    font-family: "Roboto", Arial, sans-serif;
    position: relative;
  }
  .card {
    position: absolute;
    width: 640px;
    height: 366px;
    box-shadow: 0 12px 28px rgba(0,0,0,0.18);
  }
  .card--back {
    left: 280px;
    top: 100px;
    background: var(--card-black);
    border-bottom: 5px solid var(--edge-green);
  }
  .card--front {
    left: 280px;
    top: 560px;
    background: var(--card-white);
    border-bottom: 5px solid var(--edge-green);
  }
  .brand-name {
    font-family: "Roboto", Arial, sans-serif;
    font-weight: 700;
    letter-spacing: 2px;
    line-height: 1;
  }
  .card--back .brand-name {
    position: absolute;
    left: 0; right: 0;
    top: 138px;
    text-align: center;
    font-size: 64px;
    color: var(--white);
  }
  .card--back .brand-site {
    position: absolute;
    left: 0; right: 0;
    top: 226px;
    text-align: center;
    font-size: 17px;
    color: var(--grey-text);
    letter-spacing: 0.5px;
  }
  .card--front .brand-name {
    position: absolute;
    right: 40px;
    top: 56px;
    font-size: 38px;
    color: var(--ink);
  }
  .holder {
    position: absolute;
    left: 38px;
    top: 56px;
  }
  .holder__name {
    font-family: "Montserrat", Arial, sans-serif;
    font-weight: 700;
    font-size: 20px;
    color: var(--ink);
    letter-spacing: 0.5px;
  }
  .holder__name .surname { color: var(--green); }
  .holder__role {
    font-size: 18px;
    color: var(--ink-soft);
    margin-top: 2px;
  }
  .contacts {
    list-style: none;
    margin-top: 14px;
  }
  .contacts li {
    display: flex;
    align-items: center;
    gap: 8px;
    font-size: 18px;
    color: var(--ink-soft);
    line-height: 27px;
  }
  .contacts svg { width: 15px; height: 15px; flex: none; }
  .divider {
    position: absolute;
    left: 300px;
    right: 40px;
    top: 200px;
    height: 1px;
    background: var(--ink);
  }
  .address {
    position: absolute;
    left: 345px;
    top: 236px;
    display: flex;
    gap: 8px;
    font-size: 19px;
    color: var(--ink-soft);
    line-height: 26px;
  }
  .address svg { width: 16px; height: 22px; margin-top: 2px; flex: none; }
</style>
</head>
<body>

<section class="card card--back" aria-label="Business card back">
  <p class="brand-name">HARBORKEY</p>
  <p class="brand-site">harborkey-example.ca</p>
</section>

<section class="card card--front" aria-label="Business card front">
  <div class="holder">
    <p class="holder__name">GARETH <span class="surname">LINDQVIST</span></p>
    <p class="holder__role">Operations Manager</p>
    <ul class="contacts">
      <li>
        <svg viewBox="0 0 16 16" aria-hidden="true"><path fill="#5a9a22" d="M3.6 1.5l2.3 2.6-1.2 1.8c.9 2 2.5 3.6 4.5 4.5l1.8-1.2 2.6 2.3-1.4 2.2C7 13.5 2.5 9 1.3 2.9z"/></svg>
        1 (555) 384-2917
      </li>
      <li>
        <svg viewBox="0 0 16 16" aria-hidden="true"><rect x="1" y="3" width="14" height="10" fill="#5a9a22"/><path d="M1 3.5l7 5 7-5" fill="none" stroke="#f4f4f2" stroke-width="1.3"/></svg>
        Gareth@harborkey-example.ca
      </li>
      <li>
        <svg viewBox="0 0 16 16" aria-hidden="true"><circle cx="8" cy="8" r="7" fill="#5a9a22"/><path d="M1 8h14M8 1c-3 3-3 11 0 14M8 1c3 3 3 11 0 14" fill="none" stroke="#f4f4f2" stroke-width="1"/></svg>
        www.harborkey-example.ca
      </li>
    </ul>
  </div>

  <p class="brand-name">HARBORKEY</p>

  <div class="divider"></div>

  <div class="address">
    <svg viewBox="0 0 16 22" aria-hidden="true"><path fill="#5a9a22" d="M8 0a8 8 0 0 0-8 8c0 6 8 14 8 14s8-8 8-14a8 8 0 0 0-8-8z"/><circle cx="8" cy="8" r="3" fill="#f4f4f2"/></svg>
    <p>240 Alder Lane<br>Westbrook 4021</p>
  </div>
</section>

</body>
</html>
```